Business card for Eyelash extension salon in Beverly Hills,California USA

We need new business card for our salon in Beverly Hills. The salon name is 'Lashvera' . We would like to have...Business name: Lashvera Name of person: will provide later Address 4720 N.Alder Crest Ave Beverly Hills , CA 90210 Phone: will provide later (Text only) Web: www.lashverastudio.example Snapgrid icon, Circlebook icon follow us for seasonal campaign and news @lashverastudiolounge Design should look elegant, high-end, clean, simple, cohesive with my brand. Please refer my brand board. Business name color will be metallic bronzy color. Im thinking grey background or white background. Thanks

Target Market(s)

25-35. Gender neutral. People who are in Entertainment business industry.
This is High-end Eyelash extension salon in Beverly Hills

Industry/Entity Type

Beauty Salon

Contact Information for Business Card

Business name: Lashvera
Name of person: will provide later
Address 4720 N.Alder Crest Ave Beverly Hills , CA 90210
Phone: will provide later (Text only)
Web: www.lashverastudio.example
Snapgrid icon, Circlebook icon
follow us for seasonal campaign and news @lashverastudiolounge

Requirements
Must have
• Beautiful, elegant, clean and simple look but very attractive and modern
Should not have
• We don't like too clutter, too busy designs.

```html
<!DOCTYPE html>
<html lang="en">
<head>
<meta charset="utf-8">
<title>Lashvera Business Card</title>
<link href="https://fonts.googleapis.com/css2?family=Cormorant+Garamond:wght@300;400;500&family=Playfair+Display:wght@700&family=Montserrat:wght@400&display=swap" rel="stylesheet">
<style>
  :root {
    --backdrop: #e2e2e2;
    --card-front: #fbfbfb;
    --card-back: #a8a8a8;
    --bronze: #7b5b43;
    --ink-soft: #7a7a7a;
    --rule: #9a9a9a;
    --white: #ffffff;
    --eye-tone: #d8d8d8;
  }
  * { margin: 0; padding: 0; box-sizing: border-box; }
  html, body { width: 1200px; height: 960px; overflow: hidden; }
  body { background: var(--backdrop); position: relative; font-family: "Cormorant Garamond", serif; }

  .card { position: absolute; width: 600px; height: 343px; }
  .card--front { left: 302px; top: 122px; background: var(--card-front); }
  .card--back { left: 299px; top: 495px; background: var(--card-back); }

  .eye-art {
    position: absolute; left: 258px; top: 82px; width: 84px; height: 20px;
    border-radius: 10px;
    background: linear-gradient(180deg, var(--eye-tone), #ececec);
  }

  .owner-name {
    position: absolute; left: 0; right: 0; top: 124px; text-align: center;
    font-family: "Playfair Display", serif; font-weight: 700; font-size: 22px;
    letter-spacing: 1px; color: var(--bronze);
  }
  .ruled {
    position: absolute; left: 151px; width: 292px;
    display: flex; align-items: center; gap: 6px;
  }
  .ruled::before, .ruled::after { content: ""; flex: 1; height: 1px; background: var(--rule); }
  .ruled--title { top: 152px; }
  .role {
    font-family: "Playfair Display", serif; font-size: 12px; letter-spacing: 1.5px;
    color: var(--rule);
  }
  .contact {
    position: absolute; left: 0; right: 0; top: 183px; text-align: center;
    font-size: 15px; line-height: 18px; color: var(--ink-soft); font-weight: 400;
  }
  .ruled--social { top: 243px; left: 120px; width: 360px; }
  .social {
    font-size: 12px; color: var(--ink-soft); letter-spacing: 0.5px; white-space: nowrap;
    display: flex; gap: 8px; align-items: center;
  }
  .social .dot { width: 4px; height: 4px; border-radius: 50%; background: var(--rule); }

  .brand-name {
    position: absolute; left: 0; right: 0; top: 92px; text-align: center;
    font-family: "Cormorant Garamond", serif; font-weight: 300; font-size: 124px;
    line-height: 1; color: var(--white);
  }
  .brand-place {
    position: absolute; left: 289px; top: 249px;
    font-family: "Montserrat", sans-serif; font-size: 13px; letter-spacing: 2.5px;
    color: var(--white);
  }
</style>
</head>
<body>
  <section class="card card--front">
    <div class="eye-art" role="img" aria-label="Line illustration of closed eyes with lashes"></div>
    <h1 class="owner-name">MIREILLE</h1>
    <div class="ruled ruled--title"><span class="role">OWNER</span></div>
    <p class="contact">
      4720 N.Alder Crest Ave, Beverly Hills, CA 90210<br>
      310.555.0148 | hello@lashverastudio.example | lashverastudio.example
    </p>
    <div class="ruled ruled--social">
      <span class="social">Circlebook <span class="dot"></span> Snapgrid <span class="dot"></span> Reviewly</span>
    </div>
  </section>

  <section class="card card--back">
    <h2 class="brand-name">Lashvera</h2>
    <p class="brand-place">BEVERLY HILLS</p>
  </section>
</body>
</html>
```